Federal Government Proposal Development Consulting company needs a website designed and coded

I am looking for someone to design (using an existing logo, color palette, and text fonts) and code a wordpress-based website for a Proposal Development consulting company. I have full copy for all site pages and suggestions for images/ graphics and a few example design templates to go from.

One note, from a color perspective - I included a mockup of a business card to highlight a color scheme that I tend to like - if you look at the back of the business card, the blend of the grey, blue, with the neon green highlight as a separator really seems to pop. Just a thought as you are designing the page.

I would like to see 2-3 potential design layouts, and I will select one to move forward with. Then, I would like the site to be coded for WordPress (I can provide a login to my wordpress site). I would like 1 opportunity to review the coded site and make any final tweaks.

```html
<!DOCTYPE html>
<html lang="en">
<head>
<meta charset="utf-8">
<title>Brightpath Proposals Consulting</title>
<link href="https://fonts.googleapis.com/css2?family=Alice&family=Poppins:wght@400;500;600&display=swap" rel="stylesheet">
<style>
:root{
  --navy:#0c1a4b;
  --navy-deep:#07123a;
  --mint:#2ef0c0;
  --ink:#333a44;
  --muted:#5b6270;
  --line:#d9dde3;
  --grey-bg:#f1f2f4;
  --footer:#1f2022;
  --white:#ffffff;
  --star:#f3a21b;
}
*{box-sizing:border-box;margin:0;padding:0}
html,body{width:1200px;height:4552px;overflow:hidden}
body{font-family:"Poppins",sans-serif;color:var(--ink);background:var(--white);position:relative}
.serif{font-family:"Alice",serif}
section,header,footer{position:absolute;left:0;width:1200px}
.btn{display:inline-block;border-radius:999px;font-family:"Alice",serif;font-size:17px;padding:11px 30px;text-decoration:none}
.btn-navy{background:var(--navy);color:var(--white)}
.btn-mint{background:var(--mint);color:var(--navy)}
.section-title{font-family:"Alice",serif;color:var(--navy);font-size:54px;text-align:center;font-weight:400}

/* header */
.site-header{top:0;height:120px;background:var(--white)}
.brand{position:absolute;left:64px;top:26px;display:flex;align-items:center;gap:12px}
.brand-mark{width:14px;height:14px;border-radius:50%;background:var(--navy)}
.brand-name{font-family:"Alice",serif;color:var(--navy);font-size:28px;line-height:1}
.brand-sub{font-family:"Alice",serif;color:var(--navy);font-size:14px;margin-top:4px}
.main-nav{position:absolute;left:520px;top:40px;width:620px;height:48px;background:var(--navy);border-radius:4px;display:flex;justify-content:space-around;align-items:center}
.main-nav a{color:var(--white);font-size:13px;font-weight:500;text-decoration:none;letter-spacing:.5px}

/* hero */
.hero{top:120px;height:600px}
.hero-photo{position:absolute;inset:0;background:linear-gradient(160deg,#6f8fa6 0%,#4f6f89 45%,#2f4a63 100%)}
.hero-copy{position:absolute;left:60px;top:240px;color:var(--white)}
.hero-copy h1{font-family:"Alice",serif;font-weight:400;font-size:50px;letter-spacing:1px}
.hero-copy p{font-family:"Alice",serif;font-size:27px;line-height:1.2;margin:6px 0 22px}

/* what we do */
.what-we-do{top:720px;height:810px}
.what-we-do .section-title{margin-top:48px}
.intro{width:1040px;margin:26px auto 0;font-size:12.5px;line-height:1.75;color:var(--muted);text-align:center}
.intro + .intro{margin-top:16px}
.card-row{display:grid;grid-template-columns:repeat(3,312px);gap:56px;width:1048px;margin:72px auto 0}
.offer-card{border:1px solid var(--line);border-radius:12px;box-shadow:0 4px 14px rgba(12,26,75,.08);padding:24px 20px 26px;height:400px;position:relative}
.offer-head{display:flex;align-items:center;gap:12px;height:64px}
.offer-head svg{flex:none}
.offer-head h3{font-family:"Alice",serif;font-weight:400;color:var(--navy);font-size:27px;line-height:1.1}
.offer-card p{font-size:12.5px;line-height:1.7;color:var(--muted);margin-top:16px}
.offer-card .btn{position:absolute;left:20px;bottom:26px;font-size:15px;padding:9px 26px}

/* who we are */
.who-we-are{top:1530px;height:430px;text-align:center;color:var(--white)}
.who-photo{position:absolute;inset:0;background:linear-gradient(180deg,#5b6270 0%,#434956 100%)}
.who-inner{position:relative;padding-top:74px}
.who-inner .section-title{color:var(--white)}
.who-inner p{width:1060px;margin:28px auto 30px;font-size:12.5px;line-height:1.8}
.who-inner .btn{border:1px solid rgba(255,255,255,.6)}

/* icon grids */
.services{top:1960px;height:620px;text-align:center}
.expertise{top:2580px;height:620px;background:var(--grey-bg);text-align:center}
.services .section-title,.expertise .section-title{margin-top:44px}
.icon-grid{display:grid;grid-template-columns:repeat(4,230px);gap:0 36px;width:1028px;margin:52px auto 0;row-gap:46px}
.icon-item{display:flex;flex-direction:column;align-items:center}
.icon-item span{margin-top:12px;font-family:"Alice",serif;color:var(--navy);font-size:19px;line-height:1.25}
.services .btn,.expertise .btn{margin-top:56px;font-size:15px}

/* contact */
.contact{top:3200px;height:520px;background:radial-gradient(ellipse at 50% 40%,#1a2f7a 0%,var(--navy) 55%,var(--navy-deep) 100%);text-align:center}
.contact .section-title{color:var(--white);margin-top:66px}
.contact-form{width:880px;margin:28px auto 0;display:grid;grid-template-columns:1fr 1fr;gap:16px}
.field{height:42px;background:var(--white);border-radius:10px;text-align:left;padding:11px 18px;font-size:13px;color:var(--ink)}
.field.message{grid-column:1 / -1;height:120px}
.contact .btn{margin-top:22px;font-size:15px;padding:9px 28px}

/* testimonials */
.testimonials{top:3720px;height:400px}
.testimonials .section-title{margin-top:60px}
.quote-row{display:grid;grid-template-columns:repeat(3,316px);gap:48px;width:1044px;margin:30px auto 0}
.quote-card{border:1px solid var(--line);border-radius:12px;box-shadow:0 4px 14px rgba(12,26,75,.08);height:220px;padding:18px 24px;text-align:center}
.avatar{width:58px;height:58px;border-radius:50%;background:linear-gradient(135deg,#b9c0cc,#7d8696);margin:0 auto 10px}
.quote-card p{font-size:12.5px;line-height:1.5;color:var(--ink)}
.quote-card h4{font-size:14px;font-weight:600;margin-top:8px;color:var(--ink)}
.stars{color:var(--star);font-size:15px;letter-spacing:2px}
.arrow{position:absolute;top:210px}

/* footer */
.site-footer{top:4120px;height:432px;background:var(--footer);color:var(--white)}
.foot-brand{position:absolute;left:80px;top:108px}
.foot-brand .brand-name{color:var(--white);font-size:26px}
.foot-brand .brand-sub{color:var(--white)}
.foot-brand small{display:block;font-size:11px;margin-top:18px;line-height:1.5;color:#c9ccd2}
.foot-col{position:absolute;top:50px}
.foot-col h5{font-family:"Alice",serif;font-weight:400;color:var(--mint);font-size:23px;margin-bottom:10px}
.foot-col li{list-style:none;font-family:"Alice",serif;font-size:16px;line-height:2.1}
.contact-line{display:flex;align-items:center;gap:10px;font-size:14px;line-height:2.2}
.socials{display:flex;gap:14px;margin-top:6px}
.socials i{width:24px;height:24px;border-radius:50%;background:var(--white);display:block}
</style>
</head>
<body>
<svg width="0" height="0" style="position:absolute">
  <defs>
    <symbol id="ic" viewBox="0 0 60 60">
      <circle cx="30" cy="30" r="28" fill="var(--mint)"/>
      <circle cx="30" cy="30" r="12" fill="none" stroke="var(--navy)" stroke-width="3"/>
      <path d="M30 14v6M30 40v6M14 30h6M40 30h6" stroke="var(--navy)" stroke-width="3" stroke-linecap="round"/>
    </symbol>
    <symbol id="ic-doc" viewBox="0 0 60 60">
      <circle cx="30" cy="30" r="28" fill="var(--mint)"/>
      <rect x="20" y="16" width="20" height="28" rx="2" fill="none" stroke="var(--navy)" stroke-width="3"/>
      <path d="M25 24h10M25 30h10M25 36h7" stroke="var(--navy)" stroke-width="2.5"/>
    </symbol>
    <symbol id="ic-tick" viewBox="0 0 60 60">
      <circle cx="30" cy="30" r="28" fill="var(--mint)"/>
      <path d="M19 31l7 7 15-16" fill="none" stroke="var(--navy)" stroke-width="3.5" stroke-linecap="round" stroke-linejoin="round"/>
    </symbol>
    <symbol id="ic-bars" viewBox="0 0 60 60">
      <circle cx="30" cy="30" r="28" fill="var(--mint)"/>
      <path d="M20 42V32M30 42V20M40 42V27" stroke="var(--navy)" stroke-width="5" stroke-linecap="round"/>
    </symbol>
    <symbol id="ic-line" viewBox="0 0 60 60">
      <rect x="3" y="3" width="54" height="54" rx="12" fill="none" stroke="var(--mint)" stroke-width="3"/>
      <path d="M16 40l10-10 7 6 12-14" fill="none" stroke="var(--navy)" stroke-width="3" stroke-linecap="round" stroke-linejoin="round"/>
    </symbol>
  </defs>
</svg>

<header class="site-header">
  <div class="brand">
    <div>
      <div class="brand-name">Brightpath Proposals</div>
      <div class="brand-sub">Consulting LLC</div>
    </div>
    <span class="brand-mark"></span>
  </div>
  <nav class="main-nav">
    <a href="#">HOME</a><a href="#">WORK WITH US</a><a href="#">WORK FOR US</a><a href="#">ABOUT US</a><a href="#">CONTACT</a>
  </nav>
</header>

<section class="hero">
  <div class="hero-photo" role="img" aria-label="Hands climbing a red ladder against a cloudy blue sky"></div>
  <div class="hero-copy">
    <h1>GENERATE SUCCESS</h1>
    <p>Fuel Innovation in Proposal Excellence with<br>Brightpath Proposals!</p>
    <a class="btn btn-mint" href="#">Click Here to Explore Our Services</a>
  </div>
</section>

<section class="what-we-do">
  <h2 class="section-title">What We Do</h2>
  <p class="intro">Brightpath Proposals specializes in advancing your organization through a comprehensive suite of services designed to modernize the proposal development process. From innovative Capture Management strategies that pinpoint lucrative opportunities, meticulous Proposal Development services that transform concepts into effective narratives, and cutting-edge Generative AI techniques that create domain-aware content accelerating proposal draft development, we are your dedicated partner in securing success. With a unique fusion of technical expertise and exceptional writing capabilities, we surpass industry standards and set new benchmarks for excellence.</p>
  <p class="intro">Discover a dynamic approach to proposal consulting that goes beyond conventional boundaries—choose Brightpath Proposals for solutions that <b>Enhance</b> the quality of your work, <b>Elevate</b> your corporate advantage, and <b>Expand</b> your industry presence.</p>
  <div class="card-row">
    <article class="offer-card">
      <div class="offer-head"><svg width="52" height="52"><use href="#ic-line"/></svg><h3>Capture Management</h3></div>
      <p>Elevate your business development strategy with our Capture Management services. From opportunity identification to strategic planning, our experts will guide you through a meticulous process, ensuring the pursuit aligns with your goals and positions your organization for success.</p>
      <a class="btn btn-navy" href="#">Learn More</a>
    </article>
    <article class="offer-card">
      <div class="offer-head"><svg width="52" height="52"><use href="#ic-line"/></svg><h3>Proposal Development</h3></div>
      <p>Transform your vision into winning proposals with our Proposal Development services. We specialize in persuasive narratives, clear technical solutions, and strategic pricing models, from meticulous compliance reviews to captivating executive summaries.</p>
      <a class="btn btn-navy" href="#">Learn More</a>
    </article>
    <article class="offer-card">
      <div class="offer-head"><svg width="52" height="52"><use href="#ic-line"/></svg><h3>Generative AI</h3></div>
      <p>Revolutionize your proposal writing process with our domain-aware Generative AI services. Using customer-installed tools, we leverage domain-aware artificial intelligence to generate innovative and tailored proposal content.</p>
      <a class="btn btn-navy" href="#">Learn More</a>
    </article>
  </div>
</section>

<section class="who-we-are">
  <div class="who-photo" role="img" aria-label="Team of colleagues meeting around a table in an office"></div>
  <div class="who-inner">
    <h2 class="section-title">Who We Are</h2>
    <p>We are a team of proposal professionals who bring years of federal contracting experience to every engagement. Our writers, strategists and solution architects work side by side with your staff to shape compelling, compliant responses. We listen first, plan carefully and write with purpose, so each submission reflects your strengths, your people and your mission, and gives evaluators every reason to choose you.</p>
    <a class="btn btn-navy" href="#">About Us</a>
  </div>
</section>

<section class="services">
  <h2 class="section-title">Our Services</h2>
  <div class="icon-grid">
    <div class="icon-item"><svg width="54" height="54"><use href="#ic"/></svg><span>Generative AI</span></div>
    <div class="icon-item"><svg width="54" height="54"><use href="#ic"/></svg><span>Technical Solutioning</span></div>
    <div class="icon-item"><svg width="54" height="54"><use href="#ic-bars"/></svg><span>Price to Win/ Competitive<br>Intelligence</span></div>
    <div class="icon-item"><svg width="54" height="54"><use href="#ic-bars"/></svg><span>Capture Management</span></div>
    <div class="icon-item"><svg width="54" height="54"><use href="#ic-doc"/></svg><span>Proposal Management</span></div>
    <div class="icon-item"><svg width="54" height="54"><use href="#ic-tick"/></svg><span>Compliance Reviews</span></div>
    <div class="icon-item"><svg width="54" height="54"><use href="#ic-doc"/></svg><span>Executive Summaries</span></div>
    <div class="icon-item"><svg width="54" height="54"><use href="#ic-doc"/></svg><span>Volume Lead</span></div>
  </div>
  <a class="btn btn-navy" href="#">View All Services</a>
</section>

<section class="expertise">
  <h2 class="section-title">Subject Matter Expertise</h2>
  <div class="icon-grid">
    <div class="icon-item"><svg width="54" height="54"><use href="#ic"/></svg><span>Generative AI</span></div>
    <div class="icon-item"><svg width="54" height="54"><use href="#ic"/></svg><span>Software/ Hardware<br>Engineering</span></div>
    <div class="icon-item"><svg width="54" height="54"><use href="#ic"/></svg><span>Systems Engineering</span></div>
    <div class="icon-item"><svg width="54" height="54"><use href="#ic-bars"/></svg><span>High Performance<br>Computing (HPC)</span></div>
    <div class="icon-item"><svg width="54" height="54"><use href="#ic-tick"/></svg><span>Secure Supply Chain<br>(ISO 28000 &amp; ISO 20243-1)</span></div>
    <div class="icon-item"><svg width="54" height="54"><use href="#ic-doc"/></svg><span>Logistics</span></div>
    <div class="icon-item"><svg width="54" height="54"><use href="#ic-doc"/></svg><span>Warehousing</span></div>
    <div class="icon-item"><svg width="54" height="54"><use href="#ic"/></svg><span>Information Technology<br>Support</span></div>
  </div>
  <a class="btn btn-navy" href="#">View All Expertise</a>
</section>

<section class="contact">
  <h2 class="section-title">Contact Us</h2>
  <form class="contact-form">
    <div class="field">Name</div>
    <div class="field">Email Address</div>
    <div class="field">Phone No.</div>
    <div class="field">Subject</div>
    <div class="field message">Message</div>
  </form>
  <a class="btn btn-mint" href="#">Submit Now</a>
</section>

<section class="testimonials">
  <h2 class="section-title">Testimonials</h2>
  <svg class="arrow" style="left:40px" width="16" height="24" viewBox="0 0 16 24"><path d="M12 3L4 12l8 9" fill="none" stroke="var(--ink)" stroke-width="3"/></svg>
  <svg class="arrow" style="right:40px" width="16" height="24" viewBox="0 0 16 24"><path d="M4 3l8 9-8 9" fill="none" stroke="var(--ink)" stroke-width="3"/></svg>
  <div class="quote-row">
    <article class="quote-card">
      <div class="avatar" role="img" aria-label="Client portrait"></div>
      <p>" Sed ut perspiciatis unde omnis iste natus error sit voluptatem accusantium doloremque laudantium, totam rem aperiam."</p>
      <h4>Name Heading</h4>
      <div class="stars">★★★★★</div>
    </article>
    <article class="quote-card">
      <div class="avatar" role="img" aria-label="Client portrait"></div>
      <p>" Sed ut perspiciatis unde omnis iste natus error sit voluptatem accusantium doloremque laudantium, totam rem aperiam."</p>
      <h4>Name Heading</h4>
      <div class="stars">★★★★★</div>
    </article>
    <article class="quote-card">
      <div class="avatar" role="img" aria-label="Client portrait"></div>
      <p>" Sed ut perspiciatis unde omnis iste natus error sit voluptatem accusantium doloremque laudantium, totam rem aperiam."</p>
      <h4>Name Heading</h4>
      <div class="stars">★★★★★</div>
    </article>
  </div>
</section>

<footer class="site-footer">
  <div class="foot-brand">
    <div class="brand-name">Brightpath Proposals</div>
    <div class="brand-sub">Consulting LLC</div>
    <small>Copyright © 2024 Company Name<br>All Rights Reserved</small>
  </div>
  <div class="foot-col" style="left:360px">
    <h5>Quick Links</h5>
    <ul><li>Home</li><li>Work with Us</li><li>Work for Us</li><li>About Us</li><li>Contact</li></ul>
  </div>
  <div class="foot-col" style="left:620px">
    <h5>Contact Details</h5>
    <div class="contact-line"><svg width="18" height="18" viewBox="0 0 24 24"><path d="M6 2l4 4-2 3c1 3 4 6 7 7l3-2 4 4-3 4C10 22 2 14 2 5z" fill="var(--mint)"/></svg>(555) 014-2290</div>
    <div class="contact-line"><svg width="18" height="18" viewBox="0 0 24 24"><rect x="2" y="5" width="20" height="14" rx="2" fill="var(--mint)"/><path d="M3 6l9 7 9-7" fill="none" stroke="var(--footer)" stroke-width="2"/></svg>info@brightpathproposals.com</div>
  </div>
  <div class="foot-col" style="left:888px">
    <h5>Follow Us</h5>
    <div class="socials"><i></i><i></i><i></i><i></i></div>
  </div>
</footer>
</body>
</html>
```